Create modern and sleek business card for luxury real estate company

We're a "boutique" real estate office looking for a design that gets across a highly modern luxury brand. Blacks and whites are probably the best colors unless we try a silver foil for the logo. I've attached a version of our current logo here. I'd like to swap out the current font on there with Gotham Light Regular.

I'm looking to have one side of the card have the logo with the space for our agents info on the other side.

Target Market(s)

Young professionals in a "luxury" headspace

Industry/Entity Type

Real estate

Contact Information for Business Card

A place for agent name, cell number, website. The slogan "Quietly Redefining Modern Living".

Font styles to use
Other font styles liked:
• Gotham Regular

Colors

Designer to choose only greyscale colors for use in the design.

Requirements
Must have
• Matte black as the background color. Clean lines and use of contrast. A specific design aspect that will use silver foil.
Nice to have
• Up in the air on integrating a QR code
Should not have
• Any houses or other real estate related design (ex: a clip art house)

```html
<!DOCTYPE html>
<html lang="en">
<head>
<meta charset="utf-8">
<title>Halden Realty – Business Card</title>
<link href="https://fonts.googleapis.com/css2?family=Montserrat:wght@300;400;600&display=swap" rel="stylesheet">
<style>
  :root{
    --stage:#2a2a2a;
    --card:#161616;
    --card-edge:#1f1f1f;
    --foil:#e6e6e6;
    --foil-soft:#bdbdbd;
    --emboss-line:#303030;
    --muted:#8a8a8a;
  }
  *{box-sizing:border-box;margin:0;padding:0}
  html,body{width:1200px;height:900px;overflow:hidden}
  body{
    background:var(--stage);
    font-family:'Montserrat',sans-serif;
    display:flex;flex-direction:column;align-items:center;justify-content:center;gap:56px;
  }
  .card{
    position:relative;width:640px;height:366px;
    background:linear-gradient(160deg,var(--card-edge),var(--card) 60%);
    border-radius:4px;overflow:hidden;
    box-shadow:0 18px 40px rgba(0,0,0,.45);
  }
  .brand{position:absolute;left:48px;top:44px;display:flex;align-items:center;gap:16px}
  .brand-mark{width:54px;height:54px;border:2px solid var(--foil);border-radius:50%;flex:none}
  .brand-name{
    color:var(--foil);font-weight:400;font-size:24px;letter-spacing:.14em;line-height:1.15;
    text-transform:uppercase;
  }
  .agent{position:absolute;left:48px;top:150px}
  .agent-name{color:var(--foil);font-weight:600;font-size:19px;letter-spacing:.06em;text-transform:uppercase}
  .agent-role{color:var(--foil-soft);font-weight:300;font-size:14px;margin-top:4px}
  .agent-rule{width:36px;height:2px;background:var(--foil);margin-top:10px}
  .contact{position:absolute;left:48px;top:248px;list-style:none}
  .contact li{display:flex;align-items:center;gap:10px;color:var(--foil);font-weight:400;font-size:14px;line-height:26px}
  .contact svg{width:12px;height:12px;flex:none}
  .emboss-ring{
    position:absolute;right:48px;bottom:24px;width:270px;height:270px;border-radius:50%;
    border:6px solid var(--emboss-line);
    box-shadow:inset 0 2px 3px rgba(0,0,0,.5),0 -1px 0 rgba(255,255,255,.04);
  }
  .back .brand{left:50%;top:50%;transform:translate(-50%,-62%)}
  .back .brand-mark{width:74px;height:74px;border-color:var(--emboss-line)}
  .back .brand-name{color:var(--emboss-line);font-size:32px;text-shadow:0 1px 0 rgba(255,255,255,.04)}
  .slogan{
    position:absolute;left:92px;bottom:54px;color:var(--muted);
    font-weight:300;font-size:14px;letter-spacing:.04em;
  }
</style>
</head>
<body>
  <section class="card front">
    <div class="brand">
      <span class="brand-mark"></span>
      <span class="brand-name">Halden<br>Realty</span>
    </div>
    <div class="agent">
      <p class="agent-name">Daniel Reyes</p>
      <p class="agent-role">Founder &amp; CEO</p>
      <div class="agent-rule"></div>
    </div>
    <ul class="contact">
      <li><svg viewBox="0 0 12 12"><path d="M3 1l2 2.5-1.2 1.2c.6 1.4 1.6 2.4 3 3L8 6.5 10.5 8.5 9.5 10.5C5 10 2 7 1.5 2.5z" fill="var(--foil)"/></svg>(555) 214-0377</li>
      <li><svg viewBox="0 0 12 12"><rect x="1" y="2.5" width="10" height="7" fill="none" stroke="var(--foil)"/><path d="M1 2.5l5 4 5-4" fill="none" stroke="var(--foil)"/></svg>hello@haldenrealty.com</li>
      <li><svg viewBox="0 0 12 12"><circle cx="6" cy="6" r="5" fill="none" stroke="var(--foil)"/><ellipse cx="6" cy="6" rx="2.2" ry="5" fill="none" stroke="var(--foil)"/><path d="M1 6h10" stroke="var(--foil)"/></svg>www.haldenrealty.com</li>
    </ul>
    <div class="emboss-ring"></div>
  </section>

  <section class="card back">
    <div class="brand">
      <span class="brand-mark"></span>
      <span class="brand-name">Halden<br>Realty</span>
    </div>
    <p class="slogan">Quietly Redefining Modern Living</p>
  </section>
</body>
</html>
```